RiverPine - Rebranding, Namecard, Stationary and One Page Web

Refresh logo, make it modern and design matching name card, stationary and one page web

RiverPine Information Technology (Int'l) Company Limited
松河訊息科技(國際)有限公司

Company is System Integrator, and will be providing products and services to government and enterprise organizations. Our Chief Security Officer came from top U.S. vendor, and had been working on top enterprise and government projects globally, so we want the refreshed image of the new company to have a East Cost U.S. style, with hint of technology from Silicon Valley. The company will also be representing top brands from the U.S. on information security.

Branding refresh is needed because company is being acquired and is expanding

Target Market(s)

Cyber Security

Industry/Entity Type

Information Technology

Contact Information for Business Card

Need Chinese and English

Number of Pages Required

1 page

Font styles to use
Sans Serif

Colors
0292cd
00a990

Requirements
Must have
• Modern, clean, cyber look. Must keep same colors and general look and feel of original logo. Only modernization, do not change its personality

```html
<!DOCTYPE html>
<html lang="en">
<head>
<meta charset="utf-8">
<title>RiverPine Name Card</title>
<link rel="stylesheet" href="https://fonts.googleapis.com/css2?family=Open+Sans:wght@400;600;700;800&family=Noto+Sans+TC:wght@400;500&display=swap">
<style>
  :root {
    --blue: #0292cd;
    --green: #00a990;
    --charcoal: #333436;
    --charcoal-light: #3c3d40;
    --ink: #3a3a3a;
    --paper: #ffffff;
    --backdrop: #e4e5e7;
  }
  * { box-sizing: border-box; margin: 0; padding: 0; }
  html, body { width: 1200px; height: 900px; overflow: hidden; }
  body {
    background: var(--backdrop);
    font-family: "Open Sans", Arial, sans-serif;
    position: relative;
  }
  .card {
    position: absolute;
    left: 290px;
    width: 620px;
    height: 360px;
    overflow: hidden;
    box-shadow: 0 8px 24px rgba(0,0,0,.18);
  }

  /* Front card */
  .card-front { top: 50px; background: var(--charcoal); }
  .world-map {
    position: absolute; inset: 0;
    background: radial-gradient(ellipse at 50% 45%, var(--charcoal-light) 0%, var(--charcoal) 70%);
  }
  .front-band { position: absolute; left: 0; bottom: 0; width: 620px; height: 110px; }
  .brand-lockup {
    position: absolute; left: 0; right: 0; top: 92px;
    text-align: center;
  }
  .brand-name {
    display: inline-flex; align-items: center; gap: 12px;
    font-weight: 800; font-size: 40px; letter-spacing: 2px;
    color: var(--blue);
  }
  .brand-dot { width: 16px; height: 16px; border-radius: 50%; background: var(--green); }
  .company-en {
    margin-top: 12px;
    font-size: 15px; font-weight: 600; color: var(--blue);
  }
  .company-zh {
    margin-top: 2px;
    font-family: "Noto Sans TC", "Open Sans", sans-serif;
    font-size: 15px; color: var(--green);
  }
  .front-url {
    position: absolute; right: 26px; bottom: 22px;
    font-size: 16px; font-weight: 600; color: var(--paper); letter-spacing: .3px;
  }

  /* Back card */
  .card-back { top: 480px; background: var(--paper); }
  .side-panel { position: absolute; left: 0; top: 0; width: 220px; height: 360px; }
  .side-map {
    position: absolute; left: 0; top: 0; width: 150px; height: 360px;
    background: linear-gradient(180deg, var(--charcoal-light), var(--charcoal));
    opacity: .5;
  }
  .side-name {
    position: absolute; left: 86px; top: 180px;
    transform: translate(-50%, -50%) rotate(-90deg);
    font-weight: 800; font-size: 56px; letter-spacing: 2px;
    color: var(--blue); white-space: nowrap;
  }
  .contact { position: absolute; left: 250px; top: 30px; right: 24px; color: var(--ink); }
  .person-name { font-size: 27px; font-weight: 700; letter-spacing: .5px; line-height: 1.1; }
  .person-name .given { color: var(--blue); }
  .person-name .family { color: var(--green); }
  .person-title { font-size: 18px; font-weight: 600; color: #555; }
  .address { margin-top: 40px; }
  .address svg { display: block; margin-bottom: 6px; }
  .address p { font-size: 15.5px; line-height: 1.35; }
  .contact-list { list-style: none; margin-top: 30px; }
  .contact-list li { display: flex; align-items: center; gap: 14px; font-size: 17px; line-height: 1.4; }
  .contact-list svg { flex: none; width: 16px; height: 16px; }
  .contact-list .accent { color: var(--blue); }
</style>
</head>
<body>

<section class="card card-front">
  <div class="world-map" role="img" aria-label="Faint world map texture across the dark card"></div>
  <div class="brand-lockup">
    <div class="brand-name"><span>RIVERPINE</span><span class="brand-dot"></span></div>
    <p class="company-en">RiverPine Information Technology (Int'l) Company Limited</p>
    <p class="company-zh">松河訊息科技(國際)有限公司</p>
  </div>
  <svg class="front-band" viewBox="0 0 620 110" aria-hidden="true">
    <polygon points="0,104 620,92 620,110 0,110" fill="var(--green)"/>
    <path d="M0,106 L620,98 L620,110 L0,110 Z" fill="var(--blue)"/>
    <path d="M330,96 C345,96 350,60 372,60 L620,60 L620,110 L330,110 Z" fill="var(--blue)"/>
  </svg>
  <p class="front-url">www.hkriverpine.com.hk</p>
</section>

<section class="card card-back">
  <svg class="side-panel" viewBox="0 0 220 360" aria-hidden="true">
    <path d="M0,0 L212,0 L212,110 C212,140 190,160 175,170 L175,360 L0,360 Z" fill="var(--charcoal)"/>
    <path d="M175,170 L184,164 L184,360 L175,360 Z" fill="var(--blue)"/>
  </svg>
  <div class="side-map" role="img" aria-label="Faint world map texture on the side panel"></div>
  <div class="side-name">RIVERPINE</div>

  <div class="contact">
    <h1 class="person-name"><span class="given">Daniel</span> <span class="family">Wong</span></h1>
    <p class="person-title">CEO</p>

    <div class="address">
      <svg width="18" height="16" viewBox="0 0 18 16" aria-hidden="true">
        <path d="M1,7 L17,1 L12,15 L9,9 Z M9,9 L17,1" fill="none" stroke="var(--green)" stroke-width="1.2" stroke-linejoin="round"/>
      </svg>
      <p>Room D, Unit 412, 4/F, Lok Fung Ind. Bldg,<br>No. 15 Hoi Yuen Road, Kwun Tong, Kowloon, HKSAR</p>
    </div>

    <ul class="contact-list">
      <li>
        <svg viewBox="0 0 16 16" aria-hidden="true"><path d="M4,1 L6.5,4.5 L5,6.5 C6,8.5 7.5,10 9.5,11 L11.5,9.5 L15,12 L13,15 C7,14 2,9 1,3 Z" fill="var(--blue)"/></svg>
        <span>(852) 5210 4896</span>
      </li>
      <li>
        <svg viewBox="0 0 16 16" aria-hidden="true"><rect x="1" y="3" width="14" height="10" fill="var(--blue)"/><path d="M1,3 L8,9 L15,3" fill="none" stroke="#fff" stroke-width="1.2"/></svg>
        <span>danielwong@hkriverpine.com.hk</span>
      </li>
      <li>
        <svg viewBox="0 0 16 16" aria-hidden="true"><circle cx="8" cy="8" r="7" fill="var(--blue)"/><path d="M1,8 H15 M8,1 C4,5 4,11 8,15 M8,1 C12,5 12,11 8,15" fill="none" stroke="#fff" stroke-width="1"/></svg>
        <span>www.<span class="accent">hkriverpine</span>.com.hk</span>
      </li>
    </ul>
  </div>
</section>

</body>
</html>
```